Rollers & Glides.com

Vertical Business Card with focus on branding with our icon. Information on card will be logo, persons name, position, phone number, email address and website. Use the the name Marcus Pellow, position President, phone number 480.915.2267, email Marcus@rollersandglides-demo.com, website www.rollersandglides-demo.com.

```html
<!DOCTYPE html>
<html lang="en">
<head>
<meta charset="utf-8">
<title>Rollers &amp; Glides — Business Card</title>
<link rel="stylesheet" href="https://fonts.googleapis.com/css2?family=Montserrat:wght@600;700&family=Roboto:wght@400;500&display=swap">
<style>
  :root {
    --backdrop: #cdd1d2;
    --paper: #eeeeec;
    --brand-blue: #1e4aa0;
    --ink-navy: #1b2c8c;
    --ink-dark: #2a2a2a;
    --white: #ffffff;
  }
  * { box-sizing: border-box; margin: 0; padding: 0; }
  html, body {
    width: 1200px; height: 1049px; overflow: hidden;
    background: var(--backdrop);
  }
  .stage {
    width: 1200px; height: 1049px;
    display: flex; align-items: center; justify-content: center; gap: 80px;
  }
  .card {
    width: 340px; height: 595px;
    border-radius: 3px;
    box-shadow: 0 18px 40px rgba(0,0,0,.18);
    display: flex; flex-direction: column; align-items: center;
    padding: 90px 28px 70px;
    text-align: center;
  }
  .card--front { background: var(--paper); color: var(--ink-dark); border-bottom: 3px solid var(--brand-blue); }
  .card--back { background: var(--brand-blue); color: var(--white); }

  .brand {
    display: flex; align-items: center; gap: 10px;
    font-family: "Montserrat", sans-serif; font-weight: 700;
    font-size: 26px; line-height: 1.15;
    height: 170px;
  }
  .brand__dot { width: 22px; height: 22px; border-radius: 50%; flex: none; }
  .card--front .brand { color: var(--ink-navy); }
  .card--front .brand__dot { background: var(--ink-navy); }
  .card--back .brand { color: var(--white); }
  .card--back .brand__dot { background: var(--white); }

  .person { margin-top: 70px; }
  .person__name {
    font-family: "Montserrat", sans-serif; font-weight: 700;
    font-size: 24px; letter-spacing: .5px; text-transform: uppercase;
  }
  .card--front .person__name { color: var(--ink-navy); }
  .person__role {
    font-family: "Roboto", sans-serif; font-weight: 500; font-size: 20px; margin-top: 2px;
  }
  .icons { display: flex; gap: 12px; justify-content: center; margin: 18px 0 14px; }
  .icons svg { width: 20px; height: 20px; }
  .card--front .icons { color: var(--ink-navy); }
  .card--back .icons { color: var(--white); }
  .contact {
    font-family: "Roboto", sans-serif; font-weight: 400; font-size: 15.5px; line-height: 1.45;
  }
</style>
</head>
<body>
<main class="stage">

  <article class="card card--front">
    <div class="brand"><span class="brand__dot"></span><span>Rollers &amp;<br>Glides.com</span></div>
    <div class="person">
      <p class="person__name">Marcus Pellow</p>
      <p class="person__role">President</p>
    </div>
    <div class="icons" aria-hidden="true">
      <svg viewBox="0 0 20 20"><path fill="currentColor" d="M4 2h4l1.5 4-2.2 1.6a10 10 0 0 0 5.1 5.1L14 10.5l4 1.5v4a2 2 0 0 1-2 2A14 14 0 0 1 2 4a2 2 0 0 1 2-2z"/></svg>
      <svg viewBox="0 0 20 20"><path fill="currentColor" d="M2 4h16v12H2z"/><path fill="none" stroke="var(--paper)" stroke-width="1.6" d="M2.5 4.5 10 11l7.5-6.5"/></svg>
      <svg viewBox="0 0 20 20"><circle cx="10" cy="10" r="8" fill="currentColor"/><path fill="none" stroke="var(--paper)" stroke-width="1.2" d="M2 10h16M10 2c-3 3-3 13 0 16M10 2c3 3 3 13 0 16"/></svg>
    </div>
    <div class="contact">
      <p>480.915.2267</p>
      <p>Marcus@rollersandglides-demo.com</p>
      <p>www.rollersandglides-demo.com</p>
    </div>
  </article>

  <article class="card card--back">
    <div class="brand"><span class="brand__dot"></span><span>Rollers &amp;<br>Glides.com</span></div>
    <div class="person">
      <p class="person__name">Marcus Pellow</p>
      <p class="person__role">President</p>
    </div>
    <div class="icons" aria-hidden="true">
      <svg viewBox="0 0 20 20"><path fill="currentColor" d="M4 2h4l1.5 4-2.2 1.6a10 10 0 0 0 5.1 5.1L14 10.5l4 1.5v4a2 2 0 0 1-2 2A14 14 0 0 1 2 4a2 2 0 0 1 2-2z"/></svg>
      <svg viewBox="0 0 20 20"><path fill="currentColor" d="M2 4h16v12H2z"/><path fill="none" stroke="var(--brand-blue)" stroke-width="1.6" d="M2.5 4.5 10 11l7.5-6.5"/></svg>
      <svg viewBox="0 0 20 20"><circle cx="10" cy="10" r="8" fill="currentColor"/><path fill="none" stroke="var(--brand-blue)" stroke-width="1.2" d="M2 10h16M10 2c-3 3-3 13 0 16M10 2c3 3 3 13 0 16"/></svg>
    </div>
    <div class="contact">
      <p>480.915.2267</p>
      <p>Marcus@rollersandglides-demo.com</p>
      <p>www.rollersandglides-demo.com</p>
    </div>
  </article>

</main>
</body>
</html>
```